Heritage Hollow Business Cards

Require a business card design. <br/><br/>Needs to include logo (either round or long version) plus these details:<br/>Maya Torvell<br/>Heritage Hollow<br/>maya@kelvadtrading.com.au<br/>02 6481 7395<br/>PO Box Glenwarra NSW 2791<br/>www.heritagehollow.com.au<br/><br/>I need in an editable format so that I can create for multiple staff members. <br/><br/>

Target Market(s)

We are an online store selling renovation products to home owners are builders. Looking for a classic classy design.

Industry/Entity Type

Home And Garden

Contact Information for Business Card

Maya Torvell
Heritage Hollow
maya@kelvadtrading.com.au
02 6481 7395
PO Box Glenwarra NSW 2791
www.heritagehollow.com.au

Colors

Designer to choose colors to be used in the design.

Requirements
Must have
• Must include Logo.

```html
<!DOCTYPE html>
<html lang="en">
<head>
<meta charset="utf-8">
<title>Heritage Hollow Business Cards</title>
<link rel="stylesheet" href="https://fonts.googleapis.com/css2?family=Tinos&display=swap">
<style>
  :root {
    --backdrop: #f0f0f0;
    --ink: #111111;
    --card-dark: #040606;
    --card-light: #ffffff;
    --stripe-dark: #4a4a4a;
    --stripe-bright: #ffffff;
    --stripe-light: #e8e8e9;
  }
  * { margin: 0; padding: 0; box-sizing: border-box; }
  html, body {
    width: 1200px; height: 1000px; overflow: hidden;
    background: var(--backdrop);
    font-family: "Tinos", "Times New Roman", serif;
    color: var(--ink);
  }
  .canvas { position: relative; width: 1200px; height: 1000px; }
  .card {
    position: absolute; width: 557px; height: 374px; overflow: hidden;
  }
  .card-front { left: 322px; top: 126px; background: var(--card-dark); }
  .card-back {
    left: 321px; top: 537px; background: var(--card-light);
    box-shadow: 0 0 3px rgba(0,0,0,0.12);
  }
  .stripes { position: absolute; left: 0; top: 0; width: 557px; height: 374px; }
  .front-emblem {
    position: absolute; left: 210px; top: 119px; width: 138px; height: 138px;
    border: 2px solid var(--card-light); border-radius: 50%;
    display: flex; align-items: center; justify-content: center; text-align: center;
    color: var(--card-light); font-size: 21px; line-height: 1.15;
  }
  .brand-line {
    position: absolute; left: 62px; top: 85px;
    font-size: 21px; color: var(--ink);
  }
  .staff-name {
    position: absolute; left: 64px; top: 140px;
    font-size: 43px; font-weight: 400; line-height: 1;
  }
  .contact-list { position: absolute; left: 63px; top: 205px; list-style: none; }
  .contact-item {
    display: flex; align-items: center; height: 28px; margin-bottom: 9px;
    font-size: 23px;
  }
  .contact-icon { width: 28px; height: 28px; margin-right: 14px; flex: none; }
  .website {
    position: absolute; right: 38px; top: 329px; font-size: 16px;
  }
</style>
</head>
<body>
<main class="canvas">

  <section class="card card-front" aria-label="Card front">
    <svg class="stripes" viewBox="0 0 557 374" aria-hidden="true">
      <defs>
        <clipPath id="front-corner"><polygon points="310,0 557,0 557,176"/></clipPath>
        <clipPath id="front-lower"><polygon points="380,40 557,40 557,176 440,90"/></clipPath>
      </defs>
      <g clip-path="url(#front-corner)" stroke="var(--stripe-dark)" stroke-width="7">
        <line x1="312" y1="0" x2="600" y2="205"/>
        <line x1="343" y1="0" x2="631" y2="205"/>
        <line x1="375" y1="0" x2="663" y2="205"/>
        <line x1="408" y1="0" x2="696" y2="205"/>
        <line x1="441" y1="0" x2="729" y2="205"/>
        <line x1="474" y1="0" x2="762" y2="205"/>
        <line x1="505" y1="0" x2="793" y2="205"/>
        <line x1="536" y1="0" x2="824" y2="205"/>
      </g>
      <g clip-path="url(#front-lower)" stroke="var(--stripe-bright)" stroke-width="7" stroke-dasharray="12 22">
        <line x1="312" y1="0" x2="600" y2="205"/>
        <line x1="343" y1="0" x2="631" y2="205"/>
        <line x1="375" y1="0" x2="663" y2="205"/>
        <line x1="408" y1="0" x2="696" y2="205"/>
        <line x1="441" y1="0" x2="729" y2="205"/>
        <line x1="474" y1="0" x2="762" y2="205"/>
        <line x1="505" y1="0" x2="793" y2="205"/>
      </g>
    </svg>
    <div class="front-emblem">Heritage<br>Hollow</div>
  </section>

  <section class="card card-back" aria-label="Card back">
    <svg class="stripes" viewBox="0 0 557 374" aria-hidden="true">
      <defs>
        <clipPath id="back-corner"><polygon points="198,0 557,0 557,246"/></clipPath>
      </defs>
      <g clip-path="url(#back-corner)" stroke="var(--stripe-light)" stroke-width="11">
        <line x1="205" y1="0" x2="605" y2="275"/>
        <line x1="235" y1="0" x2="635" y2="275"/>
        <line x1="265" y1="0" x2="665" y2="275"/>
        <line x1="295" y1="0" x2="695" y2="275"/>
        <line x1="325" y1="0" x2="725" y2="275"/>
        <line x1="355" y1="0" x2="755" y2="275"/>
        <line x1="385" y1="0" x2="785" y2="275"/>
        <line x1="415" y1="0" x2="815" y2="275"/>
        <line x1="445" y1="0" x2="845" y2="275"/>
        <line x1="475" y1="0" x2="875" y2="275"/>
        <line x1="505" y1="0" x2="905" y2="275"/>
        <line x1="535" y1="0" x2="935" y2="275"/>
      </g>
    </svg>

    <div class="brand-line">Heritage Hollow</div>
    <h1 class="staff-name">Maya Torvell</h1>

    <ul class="contact-list">
      <li class="contact-item">
        <svg class="contact-icon" viewBox="0 0 28 28" aria-hidden="true">
          <circle cx="14" cy="14" r="12.5" fill="none" stroke="var(--ink)" stroke-width="1.5"/>
          <rect x="7.5" y="9.5" width="13" height="9" fill="none" stroke="var(--ink)" stroke-width="1.4"/>
          <polyline points="7.5,9.5 14,15 20.5,9.5" fill="none" stroke="var(--ink)" stroke-width="1.4"/>
          <line x1="7.5" y1="18.5" x2="12" y2="13.5" stroke="var(--ink)" stroke-width="1.2"/>
          <line x1="20.5" y1="18.5" x2="16" y2="13.5" stroke="var(--ink)" stroke-width="1.2"/>
        </svg>
        <span>maya@kelvadtrading.com.au</span>
      </li>
      <li class="contact-item">
        <svg class="contact-icon" viewBox="0 0 28 28" aria-hidden="true">
          <circle cx="14" cy="14" r="12.5" fill="none" stroke="var(--ink)" stroke-width="1.5"/>
          <path d="M17.5 7.5 L19.5 9.5 L17 12 L15.5 10.5 C13 12 11.5 14 10.8 16.5 L12.3 18 L9.8 20.5 L7.8 18.5 C8.5 12.5 12 9 17.5 7.5 Z" fill="none" stroke="var(--ink)" stroke-width="1.3" stroke-linejoin="round"/>
        </svg>
        <span>02 6481 7395</span>
      </li>
      <li class="contact-item">
        <svg class="contact-icon" viewBox="0 0 28 28" aria-hidden="true">
          <circle cx="14" cy="14" r="12.5" fill="none" stroke="var(--ink)" stroke-width="1.5"/>
          <path d="M8 14 L14 8.5 L20 14 M9.5 13 V19.5 H18.5 V13" fill="none" stroke="var(--ink)" stroke-width="1.5" stroke-linejoin="round"/>
          <rect x="12.5" y="15" width="3" height="4.5" fill="var(--ink)"/>
        </svg>
        <span>PO Box Glenwarra NSW 2791</span>
      </li>
    </ul>

    <div class="website">www.heritagehollow.com.au</div>
  </section>

</main>
</body>
</html>
```